Corporate Business Card

Very professional, Modern, Not to busy, include phone address email, website
(253) 617-4930, 18761 52nd Avenue S, Kent, WA 98047, martin@plumlinegroup.com, varkoworks.com

Target Market(s)

Manufacturing

Industry/Entity Type

Aero, machining, manufacturing, Off road racing

Contact Information for Business Card

Phone, address email, website

```html
<!DOCTYPE html>
<html lang="en">
<head>
<meta charset="utf-8">
<title>Varko Works – Business Card</title>
<link href="https://fonts.googleapis.com/css2?family=Roboto:wght@400;500;700&family=Saira:wght@700&display=swap" rel="stylesheet">
<style>
  :root {
    --backdrop: #2c2c2c;
    --card-navy: #2b3866;
    --card-navy-deep: #25305a;
    --pattern-navy: #34427a;
    --text-white: #f1f1f3;
    --accent-red: #d0242a;
    --rule-grey: #d9d9de;
  }
  * { margin: 0; padding: 0; box-sizing: border-box; }
  html, body { width: 1200px; height: 1138px; overflow: hidden; }
  body {
    position: relative;
    background: var(--backdrop);
    font-family: "Roboto", Arial, sans-serif;
    color: var(--text-white);
  }
  .card {
    position: absolute;
    border-radius: 16px;
    overflow: hidden;
    background: linear-gradient(160deg, var(--card-navy) 0%, var(--card-navy-deep) 100%);
  }
  .card--front { left: 274px; top: 186px; width: 623px; height: 376px; }
  .card--back  { left: 276px; top: 608px; width: 618px; height: 374px; }

  .front-pattern {
    position: absolute; inset: 0;
    background: linear-gradient(135deg, var(--pattern-navy) 0%, var(--card-navy) 55%, var(--card-navy-deep) 100%);
  }
  .brand-name {
    position: absolute;
    font-family: "Roboto", Arial, sans-serif;
    font-weight: 700;
    color: var(--text-white);
    letter-spacing: 1px;
    white-space: nowrap;
  }
  .card--front .brand-name { left: 52px; top: 280px; font-size: 34px; }

  .holder-name {
    position: absolute; left: 34px; top: 46px;
    font-family: "Saira", "Arial Black", sans-serif;
    font-weight: 700; font-size: 25px; letter-spacing: 0.5px;
    white-space: nowrap;
  }
  .holder-name .surname { color: var(--accent-red); }

  .contact-list {
    position: absolute; left: 34px; top: 186px;
    list-style: none; font-size: 16.5px; line-height: 24.5px;
  }
  .contact-list li { display: flex; align-items: flex-start; }
  .contact-list .icon {
    width: 14px; height: 14px; margin: 5px 18px 0 0; flex: none;
    fill: var(--accent-red);
  }
  .contact-list .icon-spacer { width: 14px; margin-right: 18px; flex: none; }

  .footer-rule {
    position: absolute; left: 34px; top: 321px;
    width: 424px; height: 2px; background: var(--rule-grey);
  }
  .card--back .brand-name { right: 34px; top: 280px; font-size: 34px; }
</style>
</head>
<body>
  <section class="card card--front">
    <div class="front-pattern" role="img" aria-label="Repeating debossed company wordmark pattern in tone-on-tone navy"></div>
    <div class="brand-name">VARKO WORKS</div>
  </section>

  <section class="card card--back">
    <h1 class="holder-name">DANIEL <span class="surname">MERCER</span></h1>

    <ul class="contact-list">
      <li>
        <svg class="icon" viewBox="0 0 14 14" aria-hidden="true"><path d="M7 0a5 5 0 0 0-5 5c0 3.6 5 9 5 9s5-5.4 5-9a5 5 0 0 0-5-5zm0 7a2 2 0 1 1 0-4 2 2 0 0 1 0 4z"/></svg>
        <span>18761 52nd Avenue S,</span>
      </li>
      <li><span class="icon-spacer"></span><span>Kent, WA 98047</span></li>
      <li>
        <svg class="icon" viewBox="0 0 14 14" aria-hidden="true"><path d="M1 4c0-1.5 2.5-3 6-3s6 1.5 6 3v1.5H10V4H4v1.5H1zM3 7l2-2h4l2 2v5H3zm4 1.2a1.8 1.8 0 1 0 0 3.6 1.8 1.8 0 0 0 0-3.6z"/></svg>
        <span>(253) 617-4930</span>
      </li>
      <li>
        <svg class="icon" viewBox="0 0 14 14" aria-hidden="true"><path d="M0 2h14v10H0zm1.5 1.2v.4L7 7.5l5.5-3.9v-.4zM1.5 5v5.8h11V5L7 9z"/></svg>
        <span>martin@plumlinegroup.com</span>
      </li>
      <li>
        <svg class="icon" viewBox="0 0 14 14" aria-hidden="true"><path d="M7 0a7 7 0 1 0 0 14A7 7 0 0 0 7 0zm0 1.3c.7 0 1.6 1.7 1.8 4.4H5.2C5.4 3 6.3 1.3 7 1.3zM1.4 6.3h2.6c0 .5 0 1 .1 1.4H1.4a5.6 5.6 0 0 1 0-1.4zm3.8 0h3.6a12 12 0 0 1 0 1.4H5.2a12 12 0 0 1 0-1.4zm4.8 0h2.6a5.6 5.6 0 0 1 0 1.4H10zM7 12.7c-.7 0-1.6-1.7-1.8-4.4h3.6c-.2 2.7-1.1 4.4-1.8 4.4z"/></svg>
        <span>www.varkoworks.com</span>
      </li>
    </ul>

    <div class="footer-rule"></div>
    <div class="brand-name">VARKO WORKS</div>
  </section>
</body>
</html>
```